Flyer für Friseurin
Zielgruppe
Friseurin für Damen und Herren
Aufgabenstellung
https://lumivenhaar.de
Bitte erstelle mir anhand der Daten von der Website einen angepassten Entwurf mit Neueröffnung und geben keine Preise an sondern die kunden sollen sich direkt eingeladen führen um persönlich vor Ort vorbei zuschauen.

```html
<!DOCTYPE html>
<html lang="de">
<head>
<meta charset="utf-8">
<title>Große Eröffnung – Lumiven Haar &amp; Beauty Lounge</title>
<link rel="stylesheet" href="https://fonts.googleapis.com/css2?family=Cinzel:wght@500;600;700;800&family=Figtree:wght@400;500&display=swap">
<style>
  :root{
    --stage:#e4e4e4;
    --ink:#050505;
    --white:#ffffff;
    --gold-dark:#b8860b;
    --gold:#d9a63a;
    --gold-light:#f6e07a;
    --rose:#e8b4a0;
    --green:#55653f;
    --green-dark:#43512f;
  }
  *{margin:0;padding:0;box-sizing:border-box}
  html,body{width:1200px;height:1117px;overflow:hidden;background:var(--stage)}
  .flyer{
    position:absolute;left:218px;top:18px;width:764px;height:1080px;
    background:radial-gradient(ellipse at 60% 40%,#1a1a1a 0%,var(--ink) 70%);
    overflow:hidden;color:var(--white);
    font-family:"Figtree",sans-serif;
  }
  .serif{font-family:"Cinzel",serif}
  .brand-mark{
    position:absolute;left:0;right:0;top:72px;text-align:center;
    font-family:"Cinzel",serif;font-weight:600;font-size:30px;color:var(--gold);
    letter-spacing:1px;
  }
  .headline-top{
    position:absolute;left:0;right:0;top:146px;text-align:center;
    font-family:"Cinzel",serif;font-weight:700;font-size:64px;line-height:1;
  }
  .headline-main{
    position:absolute;left:0;right:0;top:214px;text-align:center;
    font-family:"Cinzel",serif;font-weight:700;font-size:86px;line-height:1;
    background:linear-gradient(180deg,var(--gold-light) 0%,var(--gold) 45%,var(--gold-dark) 100%);
    -webkit-background-clip:text;background-clip:text;color:transparent;
  }
  .salon-name{
    position:absolute;left:0;right:0;top:302px;text-align:center;
    font-family:"Cinzel",serif;font-weight:600;font-size:29px;line-height:1;
  }
  .intro{
    position:absolute;left:130px;width:504px;top:340px;text-align:center;
    font-size:14.5px;line-height:17px;
  }
  .welcome{position:absolute;left:92px;top:398px;width:300px}
  .welcome-kicker{font-family:"Cinzel",serif;font-weight:600;font-size:16px;line-height:20px}
  .welcome-title{font-family:"Cinzel",serif;font-weight:600;font-size:31px;line-height:32px;color:var(--rose);margin-top:3px}
  .feature-title{font-family:"Cinzel",serif;font-weight:700;font-size:17.5px;line-height:21px;color:var(--gold);margin-top:14px}
  .body-copy{font-size:13.4px;line-height:16.6px;margin-top:6px;width:280px}
  .body-copy + .body-copy{margin-top:16px}
  .salon-photo{
    position:absolute;left:375px;top:400px;width:308px;height:308px;border-radius:50%;
    border:11px solid var(--rose);
    background:radial-gradient(circle at 60% 40%,#6b4a36 0%,#3c2e2a 45%,#1b1d22 100%);
  }
  .quote-box{
    position:absolute;left:92px;top:739px;width:579px;height:121px;
    border:2px solid var(--gold);
    display:flex;align-items:center;justify-content:center;text-align:center;
    padding:0 16px;
    font-family:"Cinzel",serif;font-weight:600;font-size:18.5px;line-height:22px;
  }
  .cta{
    position:absolute;left:0;right:0;top:874px;text-align:center;
    font-family:"Cinzel",serif;font-weight:800;font-size:36px;line-height:1;
  }
  .social{
    position:absolute;left:86px;top:962px;display:flex;align-items:center;gap:9px;
  }
  .social-label{font-size:13px}
  .social-dot{width:22px;height:22px;border-radius:50%;background:var(--gold)}
  .social-handle{font-family:"Cinzel",serif;font-weight:600;font-size:22px}
  .footer-wave{position:absolute;left:0;bottom:0;width:764px;height:150px}
  .website{
    position:absolute;right:88px;top:1028px;
    font-family:"Cinzel",serif;font-weight:600;font-size:20px;letter-spacing:1px;
  }
</style>
</head>
<body>
<main class="flyer">
  <div class="brand-mark">Lumiven Haar</div>

  <h1 class="headline-top">Grosse</h1>
  <div class="headline-main">Eröffnung</div>
  <h2 class="salon-name">Lumiven Haar &amp; Beauty Lounge</h2>
  <p class="intro">Erleben Sie Schönheit und Stil in perfekter Harmonie. Unsere Experten verwandeln Ihre Träume in Realität.</p>

  <section class="welcome">
    <div class="welcome-kicker">Willkommen bei</div>
    <div class="welcome-title">Lumiven Haar &amp; Beautylounge</div>
    <div class="feature-title">Moderne Ausstattung &amp; Wohlfühlatmosphäre</div>
    <p class="body-copy">In unserem modernen Salon in Talheimerau erwarten Sie hochwertige Ausstattung und eine entspannte Atmosphäre. Unser erfahrenes Team sorgt dafür, dass Sie sich rundum wohlfühlen.</p>
    <p class="body-copy">Von klassischen Haarschnitten bis hin zu modernen Colorationen und Extensions - wir bieten Ihnen das komplette Spektrum der Friseurkunst auf höchstem Niveau.</p>
  </section>

  <div class="salon-photo" role="img" aria-label="Foto: Friseurin färbt einer Kundin im Salon die Haare"></div>

  <blockquote class="quote-box">"Mehr als nur Haare. Wir schaffen Momente der Schönheit und des Wohlgefühls, die Ihre Persönlichkeit strahlen lassen – mit Herz, Hand und Leidenschaft."</blockquote>

  <div class="cta">Ihr neuer Look wartet</div>

  <div class="social">
    <span class="social-label">Folgen Sie uns auf</span>
    <span class="social-dot"></span>
    <span class="social-handle">@LUMIVEN.HAAR</span>
  </div>

  <svg class="footer-wave" viewBox="0 0 764 150" preserveAspectRatio="none" aria-hidden="true">
    <defs>
      <linearGradient id="goldSweep" x1="0" x2="1" y1="0" y2="0">
        <stop offset="0" stop-color="#b8860b"/>
        <stop offset="0.4" stop-color="#f6d23a"/>
        <stop offset="0.75" stop-color="#c9962e"/>
        <stop offset="1" stop-color="#f6e07a"/>
      </linearGradient>
    </defs>
    <path d="M0 110 C150 150 300 140 430 90 C560 40 680 45 764 80 L764 150 L0 150 Z" fill="var(--green)"/>
    <path d="M0 88 C150 135 300 130 430 78 C560 28 680 22 764 60 L764 72 C680 40 560 48 430 96 C300 146 150 150 0 104 Z" fill="url(#goldSweep)"/>
  </svg>
  <div class="website">LUMIVENHAAR.DE</div>
</main>
</body>
</html>
```